Varnex Consulting Business card design.

See our website www.varnexconsulting.example which will give you a good idea of what we are about. The font is called 'Play'.

I'd like a standout business card in keeping with the themes and branding on the website

Target Market(s)

professionals. HR directors

Industry/Entity Type

Business

Contact Information for Business Card

Varnex Consulting PO Box 3172 Merrowdale NSW 2291 1300 485 193 Gavin Threlkeld Principal email: career@varnexconsulting.example ABN: 71203948865

Font styles to use
Other font styles liked:
• Play

Requirements
Must have
• Must have same design colours and branding as website.
• On back I'd prefer a list of the things we do which appears below the name at the header on the website

```html
<!DOCTYPE html>
<html lang="en">
<head>
<meta charset="utf-8">
<title>Varnex Consulting – Business Card</title>
<link rel="stylesheet" href="https://fonts.googleapis.com/css2?family=Play:wght@400;700&display=swap">
<style>
  :root {
    --navy: #0e2235;
    --navy-light: #1d3c55;
    --brand-blue: #2e8fd6;
    --ink: #1b2a3a;
    --text-grey: #3a3f45;
    --muted: #5c6166;
    --card-white: #f7f7f7;
    --card-grey: #dcdcdc;
    --backdrop: #e9e6e1;
  }
  * { box-sizing: border-box; margin: 0; padding: 0; }
  html, body {
    width: 1200px; height: 950px; overflow: hidden;
    background: var(--backdrop);
    font-family: "Play", sans-serif;
  }
  .stage {
    width: 1200px; height: 950px;
    display: flex; flex-direction: column;
    align-items: center; justify-content: center; gap: 40px;
  }
  .card {
    position: relative;
    width: 735px; height: 420px;
    border-radius: 4px;
    overflow: hidden;
    box-shadow: 0 8px 22px rgba(0,0,0,.18);
    background: linear-gradient(160deg, var(--card-white) 0%, #ececec 60%, var(--card-grey) 100%);
  }

  /* Back */
  .card-back .wordmark {
    position: absolute; left: 120px; top: 150px;
    font-size: 50px; letter-spacing: 3px; color: var(--ink);
    text-transform: uppercase;
  }
  .card-back .services {
    position: absolute; right: 120px; top: 228px;
    font-size: 19px; letter-spacing: .5px; color: var(--muted);
  }

  /* Front */
  .card-front .band {
    position: absolute; left: 0; top: 0; right: 0; height: 190px;
    background: linear-gradient(100deg, var(--navy) 0%, var(--navy) 55%, var(--navy-light) 75%, var(--navy) 100%);
  }
  .card-front .wordmark {
    position: absolute; left: 50px; top: 58px;
    font-size: 60px; letter-spacing: 4px; color: #ffffff;
    text-transform: uppercase; white-space: nowrap;
  }
  .contact {
    position: absolute; left: 50px; top: 232px;
    list-style: none; font-size: 20px; line-height: 30px; color: var(--text-grey);
  }
  .contact li { display: flex; align-items: center; gap: 10px; }
  .contact .address { padding-left: 28px; }
  .contact svg { width: 18px; height: 18px; fill: var(--ink); flex: none; }
  .signature {
    position: absolute; right: 50px; bottom: 62px; text-align: right;
  }
  .signature .name { font-size: 28px; font-weight: 700; color: var(--ink); letter-spacing: .5px; }
  .signature .role { font-size: 21px; color: var(--brand-blue); margin-top: 2px; }
</style>
</head>
<body>
<main class="stage">

  <section class="card card-back" aria-label="Card back">
    <div class="wordmark">Varnex Consulting</div>
    <p class="services">Coaching | Leadership | Outplacement</p>
  </section>

  <section class="card card-front" aria-label="Card front">
    <div class="band"></div>
    <div class="wordmark">Varnex Consulting</div>

    <ul class="contact">
      <li class="address">PO Box 3172 Merrowdale</li>
      <li class="address">NSW 2291</li>
      <li>
        <svg viewBox="0 0 24 24" aria-hidden="true"><path d="M6.6 10.8a15.1 15.1 0 0 0 6.6 6.6l2.2-2.2a1 1 0 0 1 1-.25 11.4 11.4 0 0 0 3.6.57 1 1 0 0 1 1 1V20a1 1 0 0 1-1 1A17 17 0 0 1 3 4a1 1 0 0 1 1-1h3.5a1 1 0 0 1 1 1c0 1.25.2 2.45.57 3.57a1 1 0 0 1-.25 1z"/></svg>
        1300 485 193
      </li>
      <li>
        <svg viewBox="0 0 24 24" aria-hidden="true"><path d="M2 5h20v14H2z M2 5l10 8 10-8" fill="var(--ink)"/><path d="M3 6.2l9 7.1 9-7.1" stroke="#fff" stroke-width="1.6" fill="none"/></svg>
        career@varnexconsulting.example
      </li>
      <li>
        <svg viewBox="0 0 24 24" aria-hidden="true"><circle cx="12" cy="12" r="10"/><path d="M2 12h20M12 2c3 3 3 17 0 20M12 2c-3 3-3 17 0 20" stroke="#fff" stroke-width="1.4" fill="none"/></svg>
        www.varnexconsulting.example
      </li>
    </ul>

    <div class="signature">
      <p class="name">Gavin Threlkeld</p>
      <p class="role">Principal</p>
    </div>
  </section>

</main>
</body>
</html>
```